High-end construction company needs a business card design

We need a modern looking business card that draws people in, is memorable and looks so good people will want to sick it on their fridges.
On the first side what is needed are:
Logo
My name - Tomasz Brelwik
Title - Managing Director
Website - www.varkelt.co.uk
Email - tomasz@varkelt.co.uk
Telephone - 020 5194 6281
Mobile - 07845139072
On the back side was is needed is a list of all the services we provide:
-Kitchen Renovations
-Bathroom Renovations
-House Renovations
-Garage Conversions
-Extensions
-Loft Conversions
-Conservatories
-Carpentry
-Tiling
-Electrical
-Plumbing & Heating
-Bricklaying
-Landscaping
-Decorating
-Plastering
We would like the colours to be the same shades as on the logo with grey or black for the words.
Target Market(s)
Anyone who needs building work done
Contact Information for Business Card
This business card is for a construction company which strives to deliver excellent service and quality.
The look and feel of the card should represent this.
Requirements
Must have
- On the first side what is needed are:
Logo
My name - Tomasz Brelwik
Title - Managing Director
Website - www.varkelt.co.uk
Email - tomasz@varkelt.co.uk
Telephone - 020 5194 6281
Mobile - 07845139072
Nice to have
- Cool looking features

```html
<!DOCTYPE html>
<html lang="en">
<head>
<meta charset="utf-8">
<title>Varkelt Construction Ltd – Business Card</title>
<link href="https://fonts.googleapis.com/css2?family=Arimo:wght@400;700&display=swap" rel="stylesheet">
<style>
  :root {
    --canvas: #f0f0f0;
    --card-light: #f7f7f7;
    --card-dark: #28531f;
    --brand-green: #5bb944;
    --name-green: #3d8a33;
    --detail-green: #68a75a;
    --service-text: #f2f5ef;
  }
  * { margin: 0; padding: 0; box-sizing: border-box; }
  html, body {
    width: 1200px; height: 1200px; overflow: hidden;
    background: var(--canvas);
    font-family: "Arimo", Arial, sans-serif;
  }
  .card { position: absolute; }
  .card-front {
    left: 208px; top: 109px; width: 767px; height: 446px;
    background: var(--card-light);
  }
  .card-back {
    left: 208px; top: 620px; width: 769px; height: 446px;
    background: var(--card-dark);
  }
  .holder { position: absolute; left: 62px; top: 154px; }
  .holder-name {
    font-size: 22px; font-weight: 700; letter-spacing: 1.2px;
    color: var(--name-green); text-transform: uppercase;
  }
  .holder-title {
    margin-top: 4px; font-size: 11.5px; color: var(--detail-green);
  }
  .contact-list { list-style: none; margin-top: 20px; color: var(--detail-green); }
  .contact-list li { display: flex; align-items: baseline; line-height: 1; }
  .contact-phone { font-size: 15px; letter-spacing: 0.6px; }
  .contact-email { font-size: 13px; margin-top: 10px; letter-spacing: 0.4px; }
  .contact-web { font-size: 11.5px; margin-top: 10px; }
  .contact-label {
    font-weight: 700; font-size: 10px; color: var(--name-green);
    width: 26px; letter-spacing: 4px;
  }
  .brand {
    position: absolute; text-align: center;
    color: var(--brand-green); font-weight: 700; line-height: 1;
  }
  .brand-name { display: block; letter-spacing: 1px; }
  .brand-sub { display: block; letter-spacing: 2px; }
  .card-front .brand { left: 490px; top: 218px; width: 190px; }
  .card-front .brand-name { font-size: 42px; }
  .card-front .brand-sub { font-size: 10.5px; margin-top: 6px; }
  .card-back .brand { left: 309px; top: 138px; width: 150px; }
  .card-back .brand-name { font-size: 34px; }
  .card-back .brand-sub { font-size: 8.5px; margin-top: 5px; }
  .service-list {
    position: absolute; left: 0; right: 0; top: 229px;
    text-align: center; color: var(--service-text);
    font-size: 15px; letter-spacing: 1.8px; line-height: 27.5px;
    white-space: pre;
  }
</style>
</head>
<body>
  <section class="card card-front" aria-label="Business card front">
    <div class="holder">
      <h1 class="holder-name">Tomasz Brelwik</h1>
      <p class="holder-title">Managing Director</p>
      <ul class="contact-list">
        <li class="contact-phone"><span class="contact-label">T:</span>020 5194 6281&nbsp;&nbsp;&nbsp;, 07845139072</li>
        <li class="contact-email"><span class="contact-label">E:</span>tomasz@varkelt.co.uk</li>
        <li class="contact-web"><span class="contact-label">W:</span>www.varkelt.co.uk</li>
      </ul>
    </div>
    <div class="brand">
      <span class="brand-name">VARKELT</span>
      <span class="brand-sub">CONSTRUCTION LTD</span>
    </div>
  </section>

  <section class="card card-back" aria-label="Business card back">
    <div class="brand">
      <span class="brand-name">VARKELT</span>
      <span class="brand-sub">CONSTRUCTION LTD</span>
    </div>
    <p class="service-list">-Carpentry  -Tiling -Electrical -Plumbing &amp; Heating
-House Renovations  -Landscaping -Decorating
-Bathroom Renovations -Kitchen Renovations  -Plastering
-Conservatories -Bricklaying -Garage Conversions
-Extensions-Loft Conversions</p>
  </section>
</body>
</html>
```